Wordpress Design Project for Employee Communications Site

We need a Wordpress design for a company that strategizes on and produces materials for employee communications. Improving employee communications at all levels of an organization can help improve overall company performance and results. The site needs to look very clean and professional; we're not afraid of white space. We like the functionality that Wordpress provides; however, we only want one "true" blog page; the other pages should give the impression of a more "static" web site - particularly the home page. I have a logo that I can provide.

I have added these comments to the discussion page:
Great question - thank you for asking it. I’ve done more research

I like the very clean and monochromatic looks to many of these. I don’t have to have monochromatic, but I do like minimal colors. Simple, clean, organized. The home page should “fit” almost entirely without scrolling. I do like fat footers that you can scroll down to. I don’t want a colored background, but any that I’ve chosen with colored backgrounds could be switched to a white background.

http://www.mirabelquennet.example/
http://pondraft.example/
http://v1.samplumworth.example/
http://howdythegoat.example/
http://stayingbrisk.example/
http://www.interiors.kelmun.example/
http://trelvmasters.example/

These last two are more corporate sites. The first one is from a well-respected consultant in my area who does a lot of what I do. And I think Harwenby does a nice job with their site. So, I want to marry the look I like with getting the content job done.

http://www.messagefuelbox.example/
http://www.harwenby.example/view/en_US/us/index.htm

Target Market(s)

Target market is mid- to large-sized companies. More than 500 employees.

Industry/Entity Type

Communications

Requirements
Must have
• Need an impactful home page. There should be a "blog" page; contact us; services; about. For starters, at least. I want fonts to be very readable - that is, either quite dark gray or black.
Nice to have
• I am loathe to include a picture of myself, but I do want some images that say, "professional" and "expert" in communications.
Should not have
• I don't want a hits counter :) (I know no one would do that!).

```html
<!DOCTYPE html>
<html lang="en">
<head>
<meta charset="utf-8">
<title>TMG – Teamwise Messaging Group</title>
<link rel="stylesheet" href="https://fonts.googleapis.com/css2?family=Oswald:wght@300;400&family=Open+Sans:wght@400;600;700&family=PT+Sans:wght@400;700&family=Arimo&display=swap">
<style>
  :root {
    --lime: #c2d93b;
    --sky: #6ec6ea;
    --ink: #3a3a3a;
    --text: #4a4a4a;
    --muted: #9a9a9a;
    --rule: #e2e2e2;
    --dot: #bdbdbd;
    --white: #ffffff;
  }
  * { margin: 0; padding: 0; box-sizing: border-box; }
  html, body { width: 1200px; height: 1100px; overflow: hidden; background: var(--white); }
  body { position: relative; font-family: "PT Sans", sans-serif; color: var(--text); }
  .top-band { position: absolute; left: 0; top: 0; width: 1200px; height: 11px; background: var(--lime); }

  .brand { position: absolute; left: 216px; top: 44px; display: flex; align-items: center; gap: 14px; }
  .brand-dot { width: 64px; height: 64px; border-radius: 50%; background: var(--sky); }
  .brand-name { font-family: "Open Sans", sans-serif; font-weight: 400; color: var(--lime); font-size: 64px; line-height: 1; letter-spacing: 4px; }
  .brand-tag { position: absolute; left: 220px; top: 114px; font-family: "Open Sans", sans-serif; font-size: 13px; color: #4b4a7a; }

  .call { position: absolute; left: 845px; top: 34px; width: 165px; height: 112px; }
  .call-disc { position: absolute; left: 2px; top: 0; width: 100px; height: 100px; border-radius: 50%; background: #d7eef8; }
  .call-disc.alt { left: 68px; background: #eef4cf; }
  .call-text { position: absolute; left: 14px; top: 16px; font-family: "Open Sans", sans-serif; font-weight: 600; color: var(--ink); font-size: 18px; line-height: 23px; }

  .main-nav { position: absolute; left: 466px; top: 164px; width: 545px; height: 43px; background: var(--sky); display: flex; }
  .main-nav a { font-family: "Oswald", sans-serif; font-weight: 300; font-size: 17px; color: #20303a; text-decoration: none; height: 43px; line-height: 43px; text-align: center; }
  .main-nav a.current { background: var(--lime); }

  .hero-shadow { position: absolute; left: 100px; top: 570px; width: 1020px; height: 60px; background: radial-gradient(ellipse at 50% 30%, rgba(0,0,0,.28), rgba(0,0,0,0) 60%); }
  .hero { position: absolute; left: 210px; top: 207px; width: 801px; height: 392px; background: linear-gradient(100deg, #dfe3e6 0%, #c9d3da 35%, #9fbfdc 60%, #d9e4ee 85%, #eef1f3 100%); }
  .hero-caption { position: absolute; left: 0; top: 126px; width: 306px; height: 110px; background: var(--lime); border-radius: 0 10px 10px 0; padding: 14px 20px; }
  .hero-title { font-family: "Oswald", sans-serif; font-weight: 300; color: var(--white); font-size: 27px; line-height: 34px; }
  .hero-sub { font-family: "Open Sans", sans-serif; color: var(--ink); font-size: 15px; line-height: 20px; margin-top: 6px; margin-left: -1px; }
  .arrow { position: absolute; top: 364px; width: 38px; height: 42px; }
  .arrow.prev { left: 129px; }
  .arrow.next { left: 1039px; }
  .pager { position: absolute; left: 580px; top: 610px; display: flex; gap: 6px; }
  .pager span { width: 13px; height: 11px; border-radius: 50%; background: var(--dot); }
  .pager span.on { background: var(--sky); }

  .col { position: absolute; width: 228px; }
  .col h2 { font-family: "Oswald", sans-serif; font-weight: 400; font-size: 19px; color: var(--ink); line-height: 26px; letter-spacing: -.2px; }
  .col p { font-family: "Arimo", sans-serif; font-size: 12px; line-height: 15.7px; letter-spacing: .6px; text-align: justify; margin-top: 12px; color: var(--text); }
  .more { display: flex; align-items: center; gap: 5px; margin-top: 14px; font-family: "Open Sans", sans-serif; font-weight: 600; font-size: 12px; color: #222; }
  .more i { width: 20px; height: 12px; border-radius: 6px; background: linear-gradient(90deg, var(--sky) 50%, var(--lime) 50%); }
  .cite { font-family: "Open Sans", sans-serif; font-weight: 700; font-size: 12px; line-height: 14.5px; text-align: right; color: var(--ink); margin-top: 10px; }
  .divider { position: absolute; width: 1px; background: var(--rule); }

  .footer-rule { position: absolute; left: 90px; top: 1038px; width: 1000px; height: 10px; background: radial-gradient(ellipse at 50% 0%, rgba(0,0,0,.18), rgba(0,0,0,0) 65%); }
  .foot-brand { position: absolute; left: 201px; top: 1054px; display: flex; align-items: center; gap: 6px; font-family: "Open Sans", sans-serif; color: var(--muted); font-size: 24px; letter-spacing: 2px; }
  .foot-brand i { width: 22px; height: 22px; border-radius: 50%; background: #c8c8c8; }
  .foot-nav { position: absolute; left: 424px; top: 1051px; font-family: "Arimo", sans-serif; font-size: 13px; color: var(--ink); }
  .foot-nav a { color: var(--ink); text-decoration: none; }
  .foot-nav b { font-weight: 400; margin: 0 14px; }
  .copyright { position: absolute; left: 441px; top: 1081px; font-family: "Arimo", sans-serif; font-size: 11px; color: var(--ink); }
  .social { position: absolute; left: 903px; top: 1050px; display: flex; gap: 4px; }
  .social span { width: 32px; height: 32px; border-radius: 50%; }
</style>
</head>
<body>
  <div class="top-band"></div>

  <header>
    <div class="brand"><span class="brand-dot"></span><span class="brand-name">TMG</span></div>
    <div class="brand-tag">Teamwise Messaging Group</div>
    <div class="call">
      <span class="call-disc alt"></span>
      <span class="call-disc"></span>
      <div class="call-text">Call Us Now<br>000 - 0000 - 000</div>
    </div>
    <nav class="main-nav">
      <a class="current" href="#" style="width:93px">Home</a>
      <a href="#" style="width:106px">About</a>
      <a href="#" style="width:124px">Services</a>
      <a href="#" style="width:106px">Blog</a>
      <a href="#" style="width:116px">Contact us</a>
    </nav>
  </header>

  <div class="hero-shadow"></div>
  <section class="hero" role="img" aria-label="Photo of colleagues in a meeting, one man writing notes beside a woman">
    <div class="hero-caption">
      <div class="hero-title">Effective Communication</div>
      <div class="hero-sub">Effective communication in the work-place is the backbone of any business.</div>
    </div>
  </section>
  <svg class="arrow prev" viewBox="0 0 38 42" aria-hidden="true"><path d="M30 2 L6 21 L30 40" fill="none" stroke="#c2d93b" stroke-width="9"/></svg>
  <svg class="arrow next" viewBox="0 0 38 42" aria-hidden="true"><path d="M8 2 L32 21 L8 40" fill="none" stroke="#c2d93b" stroke-width="9"/></svg>
  <div class="pager"><span class="on"></span><span></span><span></span><span></span></div>

  <main>
    <article class="col" style="left:209px;top:654px">
      <h2>External Communication</h2>
      <p>Effective communication in the work-place is the backbone of any business. Without it, you could miss out on important opportunities, waste time and cause your employees and custom-ers to become frustrated.</p>
      <div class="more"><i></i>Read More</div>
    </article>
    <article class="col" style="left:488px;top:654px">
      <h2>Business Growth</h2>
      <p>Effective communication in the work-place is the backbone of any business. Without it, you could miss out on important opportunities, waste time and cause your employees and custom-ers to become frustrated.</p>
      <div class="more"><i></i>Read More</div>
    </article>
    <article class="col" style="left:764px;top:654px">
      <h2>Internal Communication</h2>
      <p>Effective communication in the work-place is the backbone of any business. Without it, you could miss out on important opportunities, waste time and cause your employees and custom-ers to become frustrated.</p>
      <div class="more"><i></i>Read More</div>
    </article>

    <article class="col" style="left:209px;top:850px">
      <h2>What Customers are Saying...</h2>
      <p>TMG is a great benchmarking tool."The TMG channels offer a very effective way to communicate with geographi-cally distributed stores and in a retail environment."</p>
      <div class="cite">Marisol Thackery<br>Internal Communications<br>Manager</div>
    </article>
    <article class="col" style="left:488px;top:850px">
      <h2>Internal Social Media</h2>
      <p>TMG is a great benchmarking tool."The TMG channels offer a very effective way to communicate with geographi-cally distributed stores and in a retail environment."</p>
      <div class="cite">Specifically for employee<br>communication</div>
    </article>
    <article class="col" style="left:765px;top:850px">
      <h2>Business Growth</h2>
      <p>TMG is a great benchmarking tool."The TMG channels offer a very effective way to communicate with geographi-cally distributed stores and in a retail environment."</p>
      <div class="cite">Specifically for employee<br>communication</div>
    </article>

    <div class="divider" style="left:461px;top:676px;height:130px"></div>
    <div class="divider" style="left:737px;top:676px;height:130px"></div>
    <div class="divider" style="left:461px;top:872px;height:120px"></div>
    <div class="divider" style="left:740px;top:872px;height:120px"></div>
  </main>

  <footer>
    <div class="footer-rule"></div>
    <div class="foot-brand"><i></i>TMG</div>
    <nav class="foot-nav">
      <a href="#">Home</a><b>|</b><a href="#">About</a><b>|</b><a href="#">Services</a><b>|</b><a href="#">Blog</a><b>|</b><a href="#">Contact Us</a>
    </nav>
    <div class="copyright">All rights reserved. © Teamwise Messaging Group 2008</div>
    <div class="social"><span style="background:var(--sky)"></span><span style="background:var(--lime)"></span></div>
  </footer>
</body>
</html>
```